Create website for home automation - Control your lighting, fans, blinds etc remotely by smartphone

Plan for SHOPIFY Website - Our Clever Dwelling
Company name: Our Clever Dwelling
Company Slogan: Calm Evenings Come Naturally
Clean, Modern, Easy to Navigate, easy to maintain - not a lot of coding. We need flash technology but displaying simply what we do.
What we provide:
We will be offering wireless switch which can be added to iOS/Android App via WiFi, allowing users to remotely turn on/off connected lights, fans, security cameras, appliances, irrigation, humidifier separately from anywhere at any time.
Control your home away from home. No more wandering of your mind on those lights or appliances which you might have left switched on. No need to drive back home to check and switch them off. Save that energy, money and time just with a click of your phone no matter how far you are from home.
Replace your home electrical switches with smart switches. They retrofit existing electrical switches and allow you to make the transformation as needed.
Easy to use and intuitive app allows you to control your lights and devices just at a click. Set any kind of ambiance suiting your occasion.
Set scenes in smartphone app to group and operate your devices just at a button click. Same device can be included in more than one scene.
Collections and Products
Light Switches
Wall Plugs
Fan Switch
Pendants etc special lighting types.
Light Dimmers
Blind Controllers
Home Page:
Home page needs to telling customers what we do and how we do it in a few words to grab people.
Phone
Email
Support – Download instructions per product
Client login
Wholesale login
Promotional video to be on home screen - this is a short 1.5 - 2 min illustration introduction video to who we are and what we do - this is yet to be created)
Social media link - Facebook
Pages:
FAQ
About Us
Support/Shipping/Returns policy
Support/Installation
Blog posts
Product pages:
Description
Price
Space for where a video will be featured - how each product works/installation.
Reviews
Our competition:
http://www.brivo.com.au
https://lumigardenhub.com.au/2018/04/05/best-smart-light-switches-and-plugs/
https://www.tavelinq.com

```html
<!DOCTYPE html>
<html lang="en">
<head>
<meta charset="utf-8">
<title>About Us – Our Clever Dwelling</title>
<link rel="stylesheet" href="https://fonts.googleapis.com/css2?family=Questrial&family=Open+Sans:wght@400;600&display=swap">
<style>
  :root {
    --ink: #1c1c1c;
    --body: #3a3a3a;
    --brand: #1d3f8f;
    --accent: #1c5fb0;
    --rule: #8a8a8a;
    --frame: #e4e4e4;
    --footer: #1b1b1b;
    --footer-text: #e8e8e8;
    --footer-rule: #333333;
  }
  * { box-sizing: border-box; margin: 0; padding: 0; }
  html, body { width: 864px; height: 1200px; overflow: hidden; background: #fff; }
  body { position: relative; font-family: "Open Sans", sans-serif; color: var(--body); }

  .site-header { position: absolute; left: 0; top: 0; width: 864px; height: 108px; border-bottom: 1px solid var(--rule); }
  .brand { position: absolute; left: 58px; top: 30px; display: flex; align-items: center; gap: 8px; }
  .brand-mark { width: 26px; height: 26px; border-radius: 50%; background: var(--brand); }
  .brand-text { font-family: "Questrial", sans-serif; color: var(--brand); }
  .brand-name { font-size: 13px; font-weight: 400; line-height: 1.1; }
  .brand-slogan { font-size: 7px; letter-spacing: 0.3px; }

  .main-nav { position: absolute; top: 45px; left: 0; font-family: "Questrial", sans-serif; font-size: 14px; color: var(--ink); }
  .main-nav a { position: absolute; white-space: nowrap; color: inherit; text-decoration: none; }
  .main-nav a.current { color: var(--brand); }
  .nav-icon { position: absolute; top: 47px; }

  .page-title { position: absolute; top: 150px; left: 0; width: 864px; text-align: center; font-family: "Questrial", sans-serif; font-weight: 400; font-size: 34px; color: var(--ink); }

  .hero-frame { position: absolute; left: 81px; top: 224px; width: 702px; height: 312px; border: 4px solid var(--frame); box-shadow: 0 1px 4px rgba(0,0,0,0.12); }
  .hero-photo { width: 100%; height: 100%; background: linear-gradient(120deg, #9fb4cc 0%, #d9dde3 35%, #eef0f2 55%, #5f8fd0 78%, #c6a58e 100%); }

  .about-copy { position: absolute; left: 90px; top: 580px; width: 684px; font-size: 12px; line-height: 21.5px; text-align: justify; }
  .about-copy p { margin-bottom: 21.5px; }

  .site-footer { position: absolute; left: 0; top: 960px; width: 864px; height: 240px; background: var(--footer); border-top: 7px solid var(--accent); color: var(--footer-text); }
  .footer-col { position: absolute; top: 52px; }
  .footer-col h3 { font-size: 11.5px; font-weight: 400; letter-spacing: 0.2px; margin-bottom: 12px; }
  .footer-col li { list-style: none; font-size: 9.5px; line-height: 17px; }
  .footer-col li::before { content: "»"; margin-right: 5px; }
  .contact-list p { font-size: 9.5px; line-height: 16px; margin-bottom: 4px; }
  .social-list { display: flex; gap: 10px; margin-top: 34px; }
  .social-list span { width: 18px; height: 18px; background: var(--footer-text); border-radius: 3px; }
  .footer-rule { position: absolute; left: 62px; top: 186px; width: 736px; border-top: 1px solid var(--footer-rule); }
  .copyright { position: absolute; top: 205px; left: 0; width: 864px; text-align: center; font-size: 10px; }
</style>
</head>
<body>
  <header class="site-header">
    <div class="brand">
      <span class="brand-mark"></span>
      <div class="brand-text">
        <div class="brand-name">OUR CLEVER DWELLING</div>
        <div class="brand-slogan">Calm Evenings Come Naturally</div>
      </div>
    </div>
    <nav class="main-nav">
      <a style="left:275px">Home</a>
      <a class="current" style="left:330px">About Us</a>
      <a style="left:407px">Products</a>
      <a style="left:481px">Support</a>
      <a style="left:552px">Blog</a>
      <a style="left:601px">FAQ</a>
      <a style="left:649px">Contact</a>
    </nav>
    <svg class="nav-icon" style="left:722px" width="14" height="14" viewBox="0 0 14 14" aria-label="Search"><circle cx="5.5" cy="5.5" r="4" fill="none" stroke="#111" stroke-width="2"/><line x1="8.5" y1="8.5" x2="13" y2="13" stroke="#111" stroke-width="2.4" stroke-linecap="round"/></svg>
    <svg class="nav-icon" style="left:750px;top:42px" width="16" height="19" viewBox="0 0 16 19" aria-label="Cart"><circle cx="8" cy="4" r="3.5" fill="var(--accent)"/><path d="M1 9h14l-2 8H3z" fill="#111"/><path d="M4 9l4-4 4 4" fill="none" stroke="#111" stroke-width="1.5"/></svg>
    <svg class="nav-icon" style="left:784px" width="14" height="14" viewBox="0 0 14 14" aria-label="Account"><circle cx="7" cy="4" r="3.5" fill="#111"/><path d="M0 14c0-4 3-6 7-6s7 2 7 6z" fill="#111"/></svg>
  </header>

  <h1 class="page-title">About Us</h1>

  <div class="hero-frame">
    <div class="hero-photo" role="img" aria-label="Hand holding a smartphone showing a home control app in front of a white two-storey house"></div>
  </div>

  <section class="about-copy">
    <p>It is a long established fact that a reader will be distracted by the readable content of a page when looking at its layout. The point of using Lorem Ipsum is that it has a more-or-less normal distribution of letters, as opposed to using 'Content here, content here', making it look like readable English. Many desktop publishing packages and web page editors now use Lorem Ipsum as their default model text, and a search for 'lorem ipsum' will uncover many web sites still in their infancy.</p>
    <p>Lorem Ipsum has been the industry's standard dummy text ever since the 1500s, when an unknown printer took a galley of type and scrambled it to make a type specimen book. It has survived not only five centuries, but also the leap into electronic typesetting, remaining essentially unchanged. It was popularised in the 1960s with the release of Letraset sheets containing Lorem Ipsum passages, and more recently with desktop publishing software like Aldus PageMaker including versions of Lorem Ipsum.</p>
    <p>It is a long established fact that a reader will be distracted by the readable content of a page when looking at its layout. The point of using Lorem Ipsum is that it has a more-or-less normal distribution of letters, as opposed to using 'Content here, content here', making it look like readable English. Many desktop publishing packages and web page editors now use Lorem Ipsum as their default model text, and a search for 'lorem ipsum' will uncover many web sites still in their infancy.</p>
  </section>

  <footer class="site-footer">
    <div class="footer-col" style="left:66px">
      <h3>INFORMATION</h3>
      <ul><li>Privacy Policy</li><li>Your Account</li><li>Advanced Search</li><li>Contact Us</li></ul>
    </div>
    <div class="footer-col" style="left:258px">
      <h3>LINKS</h3>
      <ul><li>Home</li><li>About us</li><li>Products</li><li>Shop</li></ul>
    </div>
    <div class="footer-col contact-list" style="left:404px">
      <h3>CONTACT US</h3>
      <p>Address : 48 Wattlebrook Lane, Fernvale,<br>Northridge, Canada</p>
      <p>Phone : &nbsp;(03) 5550 2417, &nbsp;(04) 5550 7382</p>
      <p>Email : hello@cleverdwelling.example</p>
    </div>
    <div class="footer-col" style="left:666px;top:48px">
      <h3>FOLLOW US OUT THERE</h3>
      <div class="social-list" aria-label="Social links"><span></span><span></span><span></span><span></span></div>
    </div>
    <div class="footer-rule"></div>
    <p class="copyright">Copyright © 2018. All Rights Reserved</p>
  </footer>
</body>
</html>
```